letterhead design using our existing logo

We are a small boutique property management business based in Sydney's Northern Beaches.
We are after a sleek, simple modern letterhead (A4) incorporating our logo and its colours.
Also matching envelope (DL)
I have attached the logo with black text and white text for design options.

Target Market(s)

29-69yo Male and Female

Industry/Entity Type

Property Management

Requirements
Must have
• - Harbourline Estates logo
• - Address, number and website:
• Suite 7, 12-14 Wattlegrove Parade, Larkspur Bay NSW 2188
• Tel: Carl Dorsey 0491 570 163 Marisol Quade 0491 570 218 www.harbourlinestatesgroup.com.au
Nice to have
• sleek design that looks modern and professional
Should not have
• too many colours or too busy

```html
<!DOCTYPE html>
<html lang="en">
<head>
<meta charset="utf-8">
<title>Harbourline Estates – Stationery</title>
<link href="https://fonts.googleapis.com/css2?family=Roboto+Condensed:wght@400;500&display=swap" rel="stylesheet">
<style>
  :root {
    --teal: #137a8b;
    --ink: #161616;
    --paper: #ffffff;
    --backdrop: #a5a5a5;
    --text-grey: #333333;
  }
  * { margin: 0; padding: 0; box-sizing: border-box; }
  html, body { width: 1200px; height: 906px; overflow: hidden; }
  body {
    background: var(--backdrop);
    font-family: "Roboto Condensed", "Arial Narrow", sans-serif;
    position: relative;
  }
  .sheet { position: absolute; background: var(--paper); }

  /* A4 letterhead */
  .letterhead { left: 50px; top: 100px; width: 504px; height: 714px; }
  .brand {
    font-weight: 500;
    text-transform: uppercase;
    white-space: nowrap;
    display: flex;
    align-items: center;
    line-height: 1;
  }
  .brand-mark { display: inline-block; background: var(--teal); margin-right: 6px; }
  .letterhead .brand {
    position: absolute; right: 48px; top: 47px;
    font-size: 22px; color: var(--ink);
  }
  .letterhead .brand-mark { width: 11px; height: 11px; }
  .letterhead-footer {
    position: absolute; left: 0; right: 0; bottom: 0; height: 44px;
    background: var(--teal); color: var(--paper);
    display: flex; align-items: center; justify-content: center;
    font-size: 7px; line-height: 1.35; font-weight: 400;
  }
  .footer-group { display: flex; flex-direction: column; padding: 0 22px; }
  .footer-group + .footer-group { border-left: 1px solid rgba(255,255,255,0.7); }
  .footer-line { display: flex; align-items: center; gap: 4px; }
  .footer-line svg { width: 6px; height: 6px; fill: none; stroke: var(--paper); stroke-width: 1.2; }

  /* DL envelope front */
  .envelope-front { left: 596px; top: 142px; width: 565px; height: 282px; }
  .envelope-front .brand {
    position: absolute; left: 21px; top: 32px;
    font-size: 15px; color: var(--ink);
  }
  .envelope-front .brand-mark { width: 8px; height: 8px; margin-right: 4px; }
  .return-address {
    position: absolute; left: 22px; top: 213px;
    font-style: normal;
    font-size: 8.5px; line-height: 1.35; color: var(--text-grey);
  }
  .envelope-front .return-address { top: 71px; }

  /* DL envelope back */
  .envelope-back { left: 596px; top: 487px; width: 565px; height: 282px; }
  .envelope-flap { position: absolute; left: 0; top: 0; width: 565px; height: 92px; }
  .envelope-back .brand {
    position: absolute; left: 0; right: 0; top: 40px;
    justify-content: center; font-size: 14px; color: var(--paper);
  }
  .envelope-back .brand-mark { width: 8px; height: 8px; margin-right: 4px; background: var(--paper); }
</style>
</head>
<body>

  <section class="sheet letterhead" aria-label="A4 letterhead">
    <div class="brand"><span class="brand-mark"></span>Harbourline Estates</div>
    <footer class="letterhead-footer">
      <div class="footer-group">
        <span class="footer-line"><svg viewBox="0 0 8 8"><path d="M1 2c0 3 2 5 5 5l1-1.5-1.5-1-1 .8C3.5 5 3 4.5 2.7 3.5l.8-1L2.5 1z"/></svg>0491 570 163 (Carl Dorsey)</span>
        <span class="footer-line"><svg viewBox="0 0 8 8"><path d="M1 2c0 3 2 5 5 5l1-1.5-1.5-1-1 .8C3.5 5 3 4.5 2.7 3.5l.8-1L2.5 1z"/></svg>0491 570 218 (Marisol Quade)</span>
      </div>
      <div class="footer-group">
        <span class="footer-line"><svg viewBox="0 0 8 8"><rect x="1" y="2" width="6" height="4.5"/><path d="M1 2l3 2.5L7 2"/></svg>info@harbourlinestatesgroup.com.au</span>
        <span class="footer-line"><svg viewBox="0 0 8 8"><circle cx="4" cy="4" r="3"/><path d="M1 4h6M4 1c-1.5 2-1.5 4 0 6M4 1c1.5 2 1.5 4 0 6"/></svg>www.harbourlinestatesgroup.com.au</span>
      </div>
      <div class="footer-group">
        <span>Suite 7, 12-14 Wattlegrove Parade</span>
        <span>Larkspur Bay NSW 2188</span>
      </div>
    </footer>
  </section>

  <section class="sheet envelope-front" aria-label="DL envelope, front">
    <div class="brand"><span class="brand-mark"></span>Harbourline Estates</div>
    <address class="return-address">
      Suite 7, 12-14 Wattlegrove Parade<br>Larkspur Bay NSW 2188
    </address>
  </section>

  <section class="sheet envelope-back" aria-label="DL envelope, back">
    <svg class="envelope-flap" viewBox="0 0 565 92" aria-hidden="true">
      <path d="M0 0H565L558 6Q555 60 550 83Q548 91 540 91H25Q17 91 15 83Q8 60 2 6Z" fill="var(--teal)"/>
    </svg>
    <div class="brand"><span class="brand-mark"></span>Harbourline Estates</div>
  </section>

</body>
</html>
```